We need UI/UX design for a public, informational website for The Copper Lantern.
The pages, structure, and content scope are already defined. Designers are required to work only on the UI/UX layout of these existing pages, focusing on clarity, hierarchy, spacing, and usability. Do not add, remove, rename, or reinterpret pages or content.
The website is strictly informational only. It must not include accounts, onboarding, payments, custody, escrow administration, marketplaces, dashboards, or any transactional functionality.
Scope of work
Apply UI/UX design to the predefined website pages
Design layout for text, images, notices, and sections
Ensure consistent components and layout patterns across page types
Optimize layouts for long form, compliance focused content
Content writing, page creation, and branding changes are out of scope.
Structure reference
The complete page list, hierarchy, and content definitions are provided in the technical documentation and must be treated as the primary source of truth.
A Figma link is provided only as a light visual reference for page existence and structure:
https://meadow-knot-48203956.plumsite.example/
Designers must rely on the documentation for in depth and authoritative reference.
Brand guidelines
The Copper Lantern has existing brand guidelines and official logos, including light and dark versions. These assets will be provided and must be followed exactly. Designers must not redesign, alter, or reinterpret the brand identity.
Look and feel direction
The desired visual direction is inspired by:
https://ledgerwaltz.example/
This reference is provided only to indicate:
Institutional and enterprise tone
Clean, modern typography
Strong hierarchy and generous whitespace
Editorial, content first layouts
Do not copy branding, layouts, components, or assets from the reference site.
Hero section direction
The hero section should follow a similar structural approach to the hero used on https://ledgerwaltz.example/
, meaning:
Strong editorial framing
Clear headline hierarchy
Calm, institutional first impression
However, the background video must be Abu Dhabi focused, not generic or global. The video should visually reflect:
Abu Dhabi skyline or architectural language
Institutional, sovereign, long term infrastructure tone
Clean, slow, cinematic motion
No promotional, marketing, or lifestyle visuals
The hero must remain informational, restrained, and credible. No hype. No calls to invest. No implied participation.
Constraints
One global primary CTA only: “Continue to Halvemark” (external)
All other interactions must be informational
No visuals or language implying offers, investment, eligibility, or participation
Clear separation between informational content and any external operational platforms
Deliverables
High fidelity UI/UX designs created in Figma, covering:
Desktop layouts
Tablet layouts where relevant
Mobile layouts
Complete Figma file(s) including:
All designed pages defined in the technical documentation
A reusable component library (headers, footers, cards, notice panels, forms, CTAs, typography styles, spacing system)
Clearly defined layout grids, spacing rules, and text styles
Proper use of components and variants, not detached frames
Designs prepared for developer handoff, including:
Clear layer naming and structure
Auto layout where appropriate
Consistent use of styles and components
Responsive behavior demonstrated within Figma
Notes or annotations only where necessary for clarity
No prototypes, interactions, or motion design beyond basic layout states, unless explicitly requested. The focus is static UI/UX clarity, not animation.
A detailed technical specification document and official brand assets will be provided.
Any designs delivered outside Figma, that alter structure or content, or that ignore the defined constraints, boundaries, or tone will be rejected.

```html
<!DOCTYPE html>
<html lang="en">
<head>
<meta charset="utf-8">
<title>The Copper Lantern — Governance &amp; Project Origination Framework</title>
<link href="https://fonts.googleapis.com/css2?family=Archivo:wght@700;800&family=Roboto:wght@400;500;700&display=swap" rel="stylesheet">
<style>
:root{
  --navy:#1c1a4d;
  --ink:#141a33;
  --text:#4a4f5e;
  --purple:#5b2ea6;
  --purple-bright:#7b3fe4;
  --sky:#4aa8f5;
  --sky-panel:#55b7f7;
  --cyan:#27c3da;
  --cyan-pale:#bdeef5;
  --violet:#7449b5;
  --white:#ffffff;
  --field:#c9ced8;
}
*{box-sizing:border-box;margin:0;padding:0}
html,body{width:1200px;height:5195px;overflow:hidden}
body{font-family:"Roboto",sans-serif;color:var(--text);background:var(--white);position:relative}
.abs{position:absolute}
h1,h2,h3{font-family:"Archivo",sans-serif;font-weight:800;color:var(--ink);text-transform:uppercase;letter-spacing:-0.5px}
h2.section-title{font-size:39px;line-height:50px}
p.body{font-size:15px;line-height:28.5px;text-align:justify}
.btn{position:absolute;display:flex;align-items:center;justify-content:center;font-family:"Roboto",sans-serif;font-weight:700;font-size:12px;text-transform:uppercase;color:var(--white);letter-spacing:.2px;border-radius:3px}
.btn-sky{background:var(--sky)}
.btn-purple{background:var(--purple)}
.btn-bright{background:var(--purple-bright)}

/* Hero */
.hero{position:absolute;left:0;top:0;width:1200px;height:847px;
  background:linear-gradient(180deg,#0b1540 0%,#1b2b6b 35%,#2a3f82 52%,#121c48 62%,#0d1638 100%)}
.hero-lights{position:absolute;left:300px;top:90px;width:820px;height:460px;
  background:radial-gradient(ellipse at 45% 70%,rgba(255,190,90,.45),rgba(120,160,255,.18) 45%,transparent 70%)}
.logo{position:absolute;left:143px;top:78px;display:flex;align-items:center;gap:10px}
.logo-dot{width:14px;height:14px;border-radius:50%;background:var(--white);flex:none}
.logo-name{font-family:"Archivo",sans-serif;font-weight:700;font-size:22px;line-height:28px;color:var(--white);text-transform:uppercase;white-space:nowrap}
.nav{position:absolute;top:82px;right:145px;display:flex;gap:24px;font-size:13.5px;color:var(--white)}
.nav .active{border-bottom:2px solid var(--sky);padding-bottom:4px}
.hero-title{position:absolute;left:143px;top:582px;font-size:39px;line-height:50px;color:var(--white)}
.hero-copy{position:absolute;left:702px;top:582px;width:353px;font-size:14px;line-height:24.5px;color:var(--white);text-align:justify}
.play{position:absolute;left:1116px;top:771px;width:36px;height:36px;border-radius:50%;background:var(--white)}

/* About */
.about-title{top:935px;left:143px}
.about-copy{top:1004px;left:143px;width:497px}
.about-visual{left:664px;top:922px}

/* Governance */
.governance{position:absolute;left:0;top:1412px;width:1200px;height:625px;background:var(--cyan-pale)}
.governance .rule{position:absolute;left:0;top:0;width:1200px;height:4px;background:linear-gradient(90deg,var(--cyan),var(--cyan) 50%,var(--violet) 50%,var(--violet))}
.photo{position:absolute;border-radius:20px}

/* Ecosystem */
.ecosystem{position:absolute;left:0;top:2565px;width:1200px;height:739px;background:linear-gradient(120deg,#27c7dc 0%,#3e9cd6 35%,#6a55bd 70%,#7a46b1 100%)}
.eco-card{position:absolute;border-radius:50%;background:var(--white);text-align:center;display:flex;flex-direction:column;align-items:center;justify-content:center}
.eco-card h3{font-family:"Roboto",sans-serif;text-transform:none;font-weight:500;color:var(--ink);letter-spacing:0}
.eco-card p{color:var(--text)}

/* Contact */
.field{position:absolute;border:1.5px solid var(--field);border-radius:3px;font-size:12px;color:#555;padding:13px 15px;background:var(--white)}

/* Footer */
.footer{position:absolute;left:0;top:4825px;width:1200px;height:370px;background:var(--navy);border-top:4px solid var(--cyan)}
.footer h4{position:absolute;font-family:"Archivo",sans-serif;font-weight:700;font-size:20px;color:var(--white);text-transform:uppercase}
.footer ul{position:absolute;list-style:none;font-size:14.5px;line-height:28.5px;color:var(--white)}
.social{position:absolute;top:4955px;width:32px;height:32px;border-radius:50%;border:2px solid var(--white)}
.copyright{position:absolute;top:5132px;left:0;width:1200px;text-align:center;font-size:14px;color:var(--white)}
</style>
</head>
<body>

<!-- Hero -->
<section class="hero" role="img" aria-label="Abu Dhabi skyline at night reflected on the water">
  <div class="hero-lights"></div>
</section>
<div class="btn btn-bright" style="left:847px;top:0;width:208px;height:40px;border-radius:0 0 3px 3px">Continue to Halvemark</div>
<div class="logo"><span class="logo-dot"></span><span class="logo-name">The Copper Lantern</span></div>
<nav class="nav">
  <span class="active">Home</span><span>Framework</span><span>Projects</span><span>Halvemark</span><span>Insights</span><span>Company</span><span>Contact</span>
</nav>
<h1 class="hero-title">Governance &amp;<br>Project Origination<br>Framework</h1>
<p class="hero-copy">The Copper Lantern publishes governance standards and structural concepts for complex initiatives. Operational workflows occur on a separate platform under separate terms.</p>
<div class="btn btn-sky" style="left:702px;top:704px;width:208px;height:42px">Continue to Halvemark</div>
<div class="play"><svg width="36" height="36"><path d="M14 11 L26 18 L14 25Z" fill="#141a33"/></svg></div>

<!-- About -->
<h2 class="section-title abs about-title">The Copper Lantern</h2>
<p class="body abs about-copy">The Copper Lantern is a governance and project origination group. Its purpose is to define structural standards and oversight principles for complex initiatives that may involve multiple parties, staged execution, and long-term accountability. This website publishes those standards and explains how responsibilities are separated across governance, operations, and project-level execution. This site is informational. It does not provide onboarding, account access, eligibility checks, custody of funds, escrow administration, or transaction execution. Where operational workflows exist, they are provided through a separate operating platform under separate terms and policies.</p>
<svg class="abs about-visual" width="400" height="400" viewBox="0 0 400 400">
  <defs>
    <linearGradient id="ringA" x1="0" y1="0" x2="1" y2="1"><stop offset="0" stop-color="#27c3da"/><stop offset="1" stop-color="#5b2ea6"/></linearGradient>
    <linearGradient id="photoA" x1="0" y1="0" x2="0" y2="1"><stop offset="0" stop-color="#a9c9e3"/><stop offset=".5" stop-color="#4e8aa0"/><stop offset="1" stop-color="#2f6a6e"/></linearGradient>
  </defs>
  <path d="M200 12 A188 188 0 1 1 40 110" fill="none" stroke="url(#ringA)" stroke-width="8"/>
  <path d="M200 22 A178 178 0 0 1 370 200" fill="none" stroke="#27c3da" stroke-width="4"/>
  <circle cx="200" cy="200" r="172" fill="url(#photoA)" role="img" aria-label="Aerial view of a waterfront palace and city towers"/>
  <circle cx="96" cy="34" r="17" fill="#2f7fcf"/>
</svg>

<!-- Governance -->
<section class="governance">
  <div class="rule"></div>
  <div class="photo" role="img" aria-label="Curved glass tower with diagrid facade" style="left:83px;top:111px;width:199px;height:327px;background:linear-gradient(160deg,#c7dbe9,#6f8fae 60%,#5f6a74)"></div>
  <div class="photo" role="img" aria-label="City towers lit at night" style="left:297px;top:194px;width:201px;height:326px;background:linear-gradient(180deg,#2a3148,#5a4a3a 55%,#c9853b)"></div>
  <h2 class="section-title abs" style="left:561px;top:168px">Governance and<br>Project Origination</h2>
  <p class="body abs" style="left:561px;top:288px;width:494px">Governance in this context refers to the standards that determine how projects are structured and how oversight is described. Origination refers to the initial design and definition of an initiative, including role separation, reporting expectations, and boundary setting before execution begins. The Copper Lantern focuses on these governance-level elements rather than on operating day-to-day workflows.</p>
</section>

<!-- Role separation -->
<h2 class="section-title abs" style="left:143px;top:2158px">Clear Role Separation</h2>
<p class="body abs" style="left:143px;top:2230px;width:478px">The ecosystem is designed around clear separation of responsibilities. Governance activities belong at the framework layer. Operational workflows, where available, belong on a separate operating platform designed for process execution and recordkeeping. Assets and project execution, where applicable, belong at the project level through ring-fenced structures created for specific initiatives. This separation is intended to reduce ambiguity and help stakeholders understand who is responsible for what.</p>
<div class="abs" role="img" aria-label="Waterfront skyline of modern towers by day" style="left:710px;top:2037px;width:490px;height:528px;background:linear-gradient(180deg,#d6e6ef 0%,#a8c6d8 45%,#6f9bb5 70%,#2f6f8e 100%)"></div>

<!-- Ecosystem -->
<section class="ecosystem">
  <h2 class="section-title abs" style="left:0;width:1200px;top:90px;text-align:center;color:#fff">How the Ecosystem Works</h2>
  <p class="abs" style="left:0;width:1200px;top:164px;text-align:center;font-size:15px;color:#fff">At a high level, the ecosystem can be understood as three layers:</p>
  <svg class="abs" style="left:0;top:0" width="1200" height="739">
    <defs>
      <linearGradient id="ringB" x1="0" y1="0" x2="1" y2="1"><stop offset="0" stop-color="#27c3da"/><stop offset="1" stop-color="#4a2a9a"/></linearGradient>
    </defs>
    <circle cx="286" cy="400" r="138" fill="none" stroke="url(#ringB)" stroke-width="7" stroke-dasharray="700 200" transform="rotate(200 286 400)"/>
    <circle cx="216" cy="284" r="11" fill="#2f7fcf"/>
    <circle cx="601" cy="398" r="164" fill="none" stroke="url(#ringB)" stroke-width="7" stroke-dasharray="820 240" transform="rotate(200 601 398)"/>
    <circle cx="918" cy="400" r="138" fill="none" stroke="url(#ringB)" stroke-width="7" stroke-dasharray="700 200" transform="rotate(200 918 400)"/>
    <circle cx="848" cy="284" r="11" fill="#2f7fcf"/>
  </svg>
  <div class="eco-card" style="left:161px;top:275px;width:250px;height:250px;padding:0 34px">
    <svg width="46" height="44" viewBox="0 0 46 44"><g fill="none" stroke="#3a6fd0" stroke-width="2"><path d="M4 14 L23 3 L42 14Z"/><path d="M8 18h30M8 38h30M4 42h38"/><path d="M12 20v16M19 20v16M27 20v16M34 20v16"/></g></svg>
    <h3 style="font-size:16px;margin:8px 0 6px">Governance</h3>
    <p style="font-size:12.5px;line-height:19px">Defines standards, explains role boundaries, and publishes framework information</p>
  </div>
  <div class="eco-card" style="left:451px;top:248px;width:300px;height:300px;padding:0 44px">
    <svg width="58" height="56" viewBox="0 0 58 56"><g fill="none" stroke="#3a6fd0" stroke-width="2"><circle cx="29" cy="18" r="8"/><circle cx="29" cy="18" r="14" stroke-dasharray="6 4"/><circle cx="12" cy="40" r="5"/><circle cx="29" cy="42" r="5"/><circle cx="46" cy="40" r="5"/><path d="M4 54c0-6 16-6 16 0M21 54c0-6 16-6 16 0M38 54c0-6 16-6 16 0"/></g></svg>
    <h3 style="font-size:19px;margin:8px 0 8px">Operations</h3>
    <p style="font-size:15px;line-height:24px">Manages workflow processes such as documentation steps and record-anchored audit events through a separate platform.</p>
  </div>
  <div class="eco-card" style="left:793px;top:275px;width:250px;height:250px;padding:0 38px">
    <svg width="52" height="48" viewBox="0 0 52 48"><g fill="none" stroke="#3a6fd0" stroke-width="2"><circle cx="20" cy="10" r="6"/><path d="M10 30c0-8 20-8 20 0"/><rect x="32" y="8" width="14" height="14"/><path d="M35 15l3 3 5-6"/><path d="M4 46h44M12 36v10M40 36v10M12 36h28"/></g></svg>
    <h3 style="font-size:16px;margin:8px 0 6px">Project Execution</h3>
    <p style="font-size:12.5px;line-height:19px">Occurs at the project level through dedicated structures that hold responsibilities &amp; assets where applicable.</p>
  </div>
  <div class="btn btn-purple" style="left:496px;top:609px;width:208px;height:42px">Continue to Halvemark</div>
</section>

<!-- Escrow -->
<h2 class="section-title abs" style="left:143px;top:3402px">Independent Escrow<br>&amp; Milestone Oversight</h2>
<p class="body abs" style="left:712px;top:3400px;width:343px">Some initiatives use independent escrow arrangements to coordinate staged releases linked to milestone completion. Escrow can support execution discipline by requiring defined evidence before releases occur. Escrow does not guarantee outcomes, timelines, or success, and it is not administered by this website operator. This site describes the concept for clarity and transparency.</p>
<div class="abs" role="img" aria-label="City highway interchange and tall towers at dusk" style="left:0;top:3655px;width:599px;height:494px;background:linear-gradient(180deg,#c9c3c4 0%,#9ea6b4 40%,#6a7a8e 70%,#3c4a5c 100%)"></div>
<div class="abs" style="left:434px;top:3806px;width:621px;height:500px;background:var(--sky-panel)">
  <h2 class="section-title abs" style="left:96px;top:82px;color:#fff">Where Operational<br>Workflows Happen</h2>
  <p class="abs" style="left:96px;top:196px;width:430px;font-size:14.5px;line-height:28.5px;color:#fff">Operational workflows, including any onboarding or workflow participation where permitted, occur on a separate operating platform under separate terms and policies. If you need operational access, use the Halvemark page on this site to navigate externally. This website does not host those workflows.</p>
  <div class="btn btn-purple" style="left:96px;top:383px;width:208px;height:43px">Learn the Framework</div>
</div>

<!-- Contact -->
<h2 class="section-title abs" style="left:143px;top:4412px">Contact &amp; Inquiries</h2>
<p class="abs" style="left:143px;top:4494px;width:380px;font-size:14.5px;line-height:28.5px">If you have questions about governance framework concepts, role boundaries, or information published on this website, you can contact the team using the Contact page. Do not submit sensitive personal data through public forms.</p>
<div class="btn btn-sky" style="left:145px;top:4659px;width:208px;height:41px">Contact the Team</div>
<div class="field" style="left:641px;top:4427px;width:201px;height:45px">First Name</div>
<div class="field" style="left:853px;top:4427px;width:202px;height:45px">Last Name</div>
<div class="field" style="left:641px;top:4484px;width:201px;height:45px">Enter Email</div>
<div class="field" style="left:853px;top:4484px;width:202px;height:45px">Phone</div>
<div class="field" style="left:641px;top:4540px;width:414px;height:85px">Message</div>
<div class="btn btn-bright" style="left:641px;top:4639px;width:178px;height:43px">Submit Message</div>

<!-- Footer -->
<footer class="footer">
  <h4 style="left:145px;top:88px">Links</h4>
  <ul style="left:145px;top:123px"><li>Framework</li><li>Projects</li><li>Halvemark</li><li>Insights</li></ul>
  <ul style="left:266px;top:123px"><li>Company</li><li>Contact</li><li>Legal</li><li>Glossary</li></ul>
  <h4 style="left:426px;top:88px">Legal</h4>
  <ul style="left:426px;top:123px"><li>Legal</li><li>Terms of Use</li><li>Privacy Policy</li><li>Cookie Policy</li></ul>
  <ul style="left:571px;top:123px"><li>Disclaimer &amp; Risk Notices</li><li>Acceptable Use Policy</li><li>Accessibility Statement</li></ul>
  <h4 style="left:845px;top:88px">Social Media</h4>
</footer>
<span class="social" style="left:845px" aria-label="Social profile"></span>
<span class="social" style="left:889px" aria-label="Social profile"></span>
<span class="social" style="left:933px" aria-label="Social profile"></span>
<span class="social" style="left:977px" aria-label="Social profile"></span>
<span class="social" style="left:1021px" aria-label="Social profile"></span>
<p class="copyright">© 2026 Companyname All Rights Reserved &nbsp;|&nbsp; Privacy Policy &nbsp;|&nbsp; Terms of use</p>

</body>
</html>
```